BrindleStaffing Business Card Design

We are a staffing company finding positions for dedicated nurses and physicians.

Target Market(s)

Business Professionals

Industry/Entity Type

Staffing

Contact Information for Business Card

Gordon Pratley
Chairman
417 39th Avenue South
SAINT PETERSBURG FL 33712
813-555-4172 Mobile
813-555-8036 Fax
gpratley@brindlestaffing.com
www.brindlestaffing.com

Font styles to use
Sans Serif

Colors
fbee3e
f04a50
f37122

Requirements
Must have
• Logo Attached, see colors below. We'd like to see Yellow, Orange and Red.

```html
<!DOCTYPE html>
<html lang="en">
<head>
<meta charset="utf-8">
<title>BrindleStaffing Business Card</title>
<link rel="stylesheet" href="https://fonts.googleapis.com/css2?family=Open+Sans:wght@400;600;700;800&display=swap">
<style>
  :root {
    --bg: #6b6b6d;
    --paper: #ffffff;
    --orange: #f37122;
    --red: #f04a50;
    --yellow: #fbee3e;
    --ink: #1f1f1f;
  }
  * { margin: 0; padding: 0; box-sizing: border-box; }
  html, body { width: 1200px; height: 1134px; overflow: hidden; }
  body {
    background: var(--bg);
    font-family: "Open Sans", Arial, sans-serif;
    position: relative;
  }
  .card { position: absolute; width: 719px; height: 411px; overflow: hidden; }
  .card-front { left: 99px; top: 113px; background: var(--paper); border-radius: 22px; }
  .card-back { left: 399px; top: 605px; background: var(--orange); border-radius: 40px; }

  .brand-name { position: absolute; font-weight: 700; letter-spacing: -1px; white-space: nowrap; }
  .card-front .brand-name { left: 44px; top: 160px; font-size: 38px; color: var(--orange); }
  .card-back .brand-name { left: 0; right: 0; top: 142px; text-align: center; font-size: 60px; color: var(--paper); }

  .divider { position: absolute; left: 403px; top: 105px; width: 2px; height: 152px; background: var(--orange); opacity: .7; }
  .contact { position: absolute; left: 429px; top: 100px; color: var(--ink); font-size: 18px; line-height: 27px; }
  .address { margin-bottom: 20px; }
  .contact-line { display: flex; align-items: center; gap: 9px; height: 28px; }
  .contact-line svg { width: 17px; height: 17px; flex: none; }

  .waves { position: absolute; left: 0; top: 0; width: 719px; height: 411px; }
  .holder { position: absolute; right: 52px; top: 346px; text-align: center; color: var(--paper); }
  .holder-name { font-size: 25px; font-weight: 700; line-height: 30px; }
  .holder-title { font-size: 21px; line-height: 26px; }

  .web-address { position: absolute; left: 0; right: 0; top: 256px; text-align: center; color: var(--paper); font-size: 22px; letter-spacing: 2.5px; }
  .web-address b { font-weight: 700; }
</style>
</head>
<body>
  <section class="card card-front">
    <div class="brand-name">BrindleStaffing</div>
    <div class="divider"></div>
    <div class="contact">
      <div class="address">417 39th Avenue South<br>Saint Petersburg FL 33712</div>
      <div class="contact-line">
        <svg viewBox="0 0 16 16"><circle cx="8" cy="8" r="7" fill="none" stroke="var(--orange)" stroke-width="1.5"/><path d="M5.5 4.5l1.5 1.6-.8 1c.5 1 1.3 1.8 2.3 2.3l1-.8 1.6 1.5-1.1 1.4c-2.7-.5-4.6-2.5-5.3-5.3z" fill="var(--orange)"/></svg>
        <span>813-555-4172</span>
      </div>
      <div class="contact-line">
        <svg viewBox="0 0 16 16"><path d="M1 6l7-4 7 4v8H1z" fill="var(--orange)"/><path d="M2 6.5l6 4 6-4" fill="none" stroke="#fff" stroke-width="1.3"/></svg>
        <span>gpratley@brindlestaffing.com</span>
      </div>
      <div class="contact-line">
        <svg viewBox="0 0 16 16" fill="none" stroke="var(--orange)" stroke-width="1.2"><circle cx="8" cy="8" r="6.5"/><ellipse cx="8" cy="8" rx="3" ry="6.5"/><path d="M1.5 8h13M2.5 4.8h11M2.5 11.2h11"/></svg>
        <span>www.brindlestaffing.com</span>
      </div>
    </div>
    <svg class="waves" viewBox="0 0 719 411">
      <path d="M0 348 C160 362 330 356 450 326 C560 300 660 302 719 322 L719 330 C660 310 560 309 455 334 C330 366 160 370 0 357 Z" fill="var(--red)"/>
      <path d="M0 368 C160 380 320 372 440 340 C330 390 190 406 0 411 Z" fill="var(--yellow)"/>
      <path d="M260 411 C400 396 450 344 540 330 C630 318 690 322 719 334 L719 411 Z" fill="var(--orange)"/>
    </svg>
    <div class="holder">
      <div class="holder-name">Gordon Pratley</div>
      <div class="holder-title">Title</div>
    </div>
  </section>

  <section class="card card-back">
    <div class="brand-name">BrindleStaffing</div>
    <div class="web-address">www.<b>brindlestaffing</b>.com</div>
  </section>
</body>
</html>
```